Harbour Crest Estate Group

The card is to be black

On the front it will say "Harbour Crest"
And just under it in smaller writing "Property Group" in dark brown or rose gold

Darren Keswick
0471 568 214
Admin@hbrcrestgroup.example

On the back it is to say Harbour Crest Estate group same style as the front but smaller.
And then under that say:
Electrical
General Maintenance
Building works & construction
Energy Consulants

Target Market(s)

Industry/Entity Type

Electrical

Contact Information for Business Card

The card is to be black

Darren Keswick
0471 568 214
Admin@hbrcrestgroup.example

And then under that say:
Electrical
General Maintenance
Energy Consulants

And somewhere else put residential domestic and industrial

Font styles to use
Serif

Requirements
Should not have
• No pictures of tools etc just a plain sleek card

```html
<!DOCTYPE html>
<html lang="en">
<head>
<meta charset="utf-8">
<title>Harbour Crest Property Group – Business Card</title>
<link rel="stylesheet" href="https://fonts.googleapis.com/css2?family=Oswald:wght@500;600&family=Lato:wght@400;700;900&display=swap">
<style>
  :root {
    --stage: #2a2a2c;
    --card-top: #2b2a2c;
    --card-bottom: #141415;
    --white: #f4f4f4;
    --rose: #b16b79;
    --rose-soft: #8e5a64;
    --skyline: #e6e6e6;
    --muted: #d9d9d9;
  }
  * { box-sizing: border-box; margin: 0; padding: 0; }
  html, body {
    width: 1200px; height: 997px; overflow: hidden;
    background: var(--stage);
  }
  .stage {
    position: relative; width: 1200px; height: 997px;
  }
  .card {
    position: absolute; left: 290px;
    width: 620px; height: 354px;
    border-radius: 18px; overflow: hidden;
    background: linear-gradient(160deg, var(--card-top), var(--card-bottom));
    box-shadow: 0 18px 40px rgba(0,0,0,.55);
    color: var(--white);
    font-family: "Lato", sans-serif;
  }
  .card--back { top: 112px; }
  .card--front { top: 530px; }

  .skyline {
    position: absolute; left: 0; right: 0; bottom: 0;
    height: 64px; background: var(--skyline);
  }

  .wordmark { position: absolute; left: 0; right: 0; text-align: center; }
  .wordmark__name {
    font-family: "Oswald", sans-serif; font-weight: 600;
    color: var(--white); letter-spacing: 1px; line-height: 1;
  }
  .wordmark__tag {
    font-family: "Lato", sans-serif; font-weight: 700;
    color: var(--rose); text-transform: uppercase; line-height: 1;
  }

  /* Front */
  .card--front .wordmark { top: 62px; }
  .card--front .wordmark__name { font-size: 64px; }
  .card--front .wordmark__tag { font-size: 19px; letter-spacing: 7px; margin-top: 12px; }

  .person { position: absolute; right: 338px; top: 204px; text-align: right; }
  .person__name { font-weight: 900; font-size: 19px; letter-spacing: .5px; text-transform: uppercase; }
  .person__role { color: var(--rose); font-size: 17px; margin-top: 3px; }

  .divider {
    position: absolute; left: 304px; top: 180px;
    width: 2px; height: 82px;
    background: linear-gradient(var(--rose), transparent);
  }
  .contact { position: absolute; left: 326px; top: 188px; list-style: none; }
  .contact li {
    display: flex; align-items: center; gap: 10px;
    font-size: 16px; color: var(--muted); margin-bottom: 12px;
  }
  .contact svg { width: 18px; height: 14px; fill: var(--rose); flex: none; }

  /* Back */
  .card--back .wordmark { top: 44px; }
  .card--back .wordmark__name { font-size: 46px; }
  .card--back .wordmark__tag { font-size: 14px; letter-spacing: 5px; margin-top: 8px; }

  .services-rule {
    position: absolute; left: 40px; right: 40px; top: 152px;
    display: flex; align-items: center; gap: 14px;
  }
  .services-rule::before, .services-rule::after {
    content: ""; flex: 1; height: 2px; background: var(--rose-soft);
  }
  .services-rule h2 {
    font-size: 14px; font-weight: 900; letter-spacing: 1px;
    text-transform: uppercase; color: var(--white);
  }
  .services {
    position: absolute; left: 140px; top: 186px;
    display: grid; grid-template-columns: 190px 230px; row-gap: 10px;
    list-style: none;
  }
  .services li {
    font-size: 15px; color: var(--muted);
    display: flex; align-items: center; gap: 9px;
  }
  .services li::before {
    content: ""; width: 6px; height: 6px; border-radius: 50%;
    background: var(--rose);
  }
</style>
</head>
<body>
<main class="stage">

  <section class="card card--back" aria-label="Card back">
    <div class="wordmark">
      <p class="wordmark__name">HARBOUR CREST</p>
      <p class="wordmark__tag">Property Group</p>
    </div>
    <div class="services-rule"><h2>Our Services</h2></div>
    <ul class="services">
      <li>Electrical</li>
      <li>Energy Consultants</li>
      <li>General Maintenance</li>
      <li>Building works &amp; construction</li>
    </ul>
    <div class="skyline" role="img" aria-label="Light city skyline silhouette along the card edge"></div>
  </section>

  <section class="card card--front" aria-label="Card front">
    <div class="wordmark">
      <p class="wordmark__name">HARBOUR CREST</p>
      <p class="wordmark__tag">Property Group</p>
    </div>
    <div class="person">
      <p class="person__name">Darren Keswick</p>
      <p class="person__role">Director</p>
    </div>
    <span class="divider"></span>
    <ul class="contact">
      <li>
        <svg viewBox="0 0 18 14" aria-hidden="true"><path d="M1 4c0-2 3-3 8-3s8 1 8 3v1h-4V3.5H5V5H1zM4 6h10l2 7H2z"/></svg>
        0471 568 214
      </li>
      <li>
        <svg viewBox="0 0 18 14" aria-hidden="true"><path d="M0 0h18v14H0z M1.5 1.5 9 8l7.5-6.5" stroke="#1a1a1b" stroke-width="1.4"/></svg>
        Admin@hbrcrestgroup.example
      </li>
    </ul>
    <div class="skyline" role="img" aria-label="Light city skyline silhouette along the card edge"></div>
  </section>

</main>
</body>
</html>
```